Artisan Food and Beverage company needs label for various product

We are an artisan food and beverage company with a range of different snacks, and beverages, such as chips, cold brew coffee and spreads. Because of this, we have different types of packaging - jars, pouches, bottles.
We are looking for a general label design for our different product ranges. We want to have a design that is adaptable to our different packaging containers but that will also distinguish each product from each other. Eg. Different colors for each product range
Our idea is to have the same general look for all but change the color of the border or sides(?) for each product range, We are thinking of something like this:
1. Border: different color per product range (see the collage pic and the screenshot taken from the Pixel Harbor website)
2. Product Category: Eg. Ice Cold Brew , Cheese Dips
- Same size font and type even if one is a pouch and 1 is a flask
3. Product Flavour: Eg. Mocha Latte, Cheddar and Garlic Dip
- Same size font and type even if different packaging (smaler size font
than the product category name
We have added sample pictures of a store label that fits different containers (collage pic) , as well as sample pics of our different packaging containers. We will also have jars for our spreads similar to the jar pic at the top of the collage.
If the design can be editable and the background color (or side color like the one we took a screenshot of here in the website of the crunchy sauce label - pardon that the drop down menu was taken), that is what we have in mind. We should also be able to edit the size so the best pf the whole label so maybe a rectangular label is best.
The "Chef Tolby's" is our official logo.
*Credits to the artist of the Pixel Harbor sample labels we took a screenshot of from the website.

```html
<!DOCTYPE html>
<html lang="en">
<head>
<meta charset="utf-8">
<title>Chef Tolby's Ice Cold Brew Labels</title>
<link href="https://fonts.googleapis.com/css2?family=Roboto+Slab:wght@500;700&family=Josefin+Sans:wght@600;700&family=Oswald:wght@400;500&display=swap" rel="stylesheet">
<style>
  :root {
    --page: #d9d4cd;
    --brown: #93673f;
    --brown-light: #a67a4f;
    --brown-dark: #7d5533;
    --cream: #f3f0dc;
    --cream-deep: #e6e3cd;
    --ink: #3b3733;
    --shadow-tan: #d3c8ac;
    --accent: #c98a45;
  }
  * { margin: 0; padding: 0; box-sizing: border-box; }
  html, body { width: 1200px; height: 1200px; overflow: hidden; }
  body { background: var(--page); position: relative; }

  .label {
    position: absolute;
    top: 324px;
    width: 540px;
    height: 552px;
    overflow: hidden;
  }
  .label--classic { left: 40px; background: linear-gradient(90deg, var(--brown-dark), var(--brown-light) 45%, var(--brown) 80%, var(--brown-dark)); }
  .label--modern { left: 620px; background: linear-gradient(90deg, var(--cream-deep), var(--cream) 40%, var(--cream) 70%, var(--cream-deep)); }

  .frame { position: absolute; left: 79px; top: 42px; width: 383px; height: 474px; }
  .frame svg { position: absolute; inset: 0; }

  .brand {
    position: absolute; left: 0; right: 0;
    display: flex; justify-content: center; align-items: center; gap: 8px;
    font-family: "Roboto Slab", serif; font-weight: 700; color: var(--accent);
  }
  .brand__dot { width: 16px; height: 16px; border-radius: 50%; background: var(--accent); }

  .category, .range { position: absolute; left: 0; right: 0; text-align: center; line-height: 1; }
  .label--classic .category { font-family: "Roboto Slab", serif; font-weight: 700; color: var(--ink); font-size: 48px; letter-spacing: 1px; text-shadow: 2px 2px 0 var(--shadow-tan); }
  .label--classic .range { font-family: "Roboto Slab", serif; font-weight: 700; color: var(--brown); font-size: 66px; letter-spacing: 9px; text-shadow: 3px 3px 0 var(--shadow-tan); }
  .label--modern .category { font-family: "Josefin Sans", sans-serif; font-weight: 600; color: var(--ink); font-size: 82px; text-shadow: 3px 3px 0 var(--shadow-tan); }
  .label--modern .range { font-family: "Josefin Sans", sans-serif; font-weight: 700; color: var(--brown); font-size: 104px; letter-spacing: 10px; text-shadow: 4px 4px 0 var(--shadow-tan); }

  .dots { position: absolute; left: 0; right: 0; display: flex; justify-content: center; align-items: center; gap: 13px; }
  .dots span { border-radius: 50%; background: var(--brown); display: block; }

  .flavour { font-family: "Oswald", sans-serif; font-weight: 500; color: var(--cream); text-align: center; letter-spacing: 1px; }
  .volume { position: absolute; left: 0; right: 0; text-align: center; font-family: "Oswald", sans-serif; font-weight: 400; color: var(--ink); }

  .ribbon { position: absolute; left: 80px; top: 366px; width: 224px; height: 46px; }
  .ribbon svg { position: absolute; inset: 0; }
  .ribbon .flavour { position: absolute; left: 0; right: 0; top: 6px; font-size: 20px; }

  .flavour-band { position: absolute; left: 0; right: 0; top: 427px; height: 62px; background: var(--brown); display: flex; align-items: center; justify-content: center; }
  .flavour-band .flavour { font-size: 40px; }
</style>
</head>
<body>

  <section class="label label--classic">
    <div class="frame">
      <svg viewBox="0 0 383 474" width="383" height="474">
        <path d="M30 0 H353 A30 30 0 0 0 383 30 V444 A30 30 0 0 0 353 474 H30 A30 30 0 0 0 0 444 V30 A30 30 0 0 0 30 0 Z" fill="var(--cream)"/>
        <path d="M36 12 H347 A24 24 0 0 0 371 36 V438 A24 24 0 0 0 347 462 H36 A24 24 0 0 0 12 438 V36 A24 24 0 0 0 36 12 Z" fill="none" stroke="var(--brown)" stroke-width="2"/>
        <line x1="28" y1="83" x2="28" y2="398" stroke="var(--brown)" stroke-width="5" stroke-linecap="round" stroke-dasharray="0 21"/>
        <line x1="355" y1="83" x2="355" y2="398" stroke="var(--brown)" stroke-width="5" stroke-linecap="round" stroke-dasharray="0 21"/>
      </svg>

      <div class="brand" style="top:72px; font-size:26px;"><span class="brand__dot"></span>Chef Tolby's</div>
      <div class="category" style="top:171px;">ICE COLD</div>
      <div class="range" style="top:232px;">BREW</div>
      <div class="dots" style="top:334px;">
        <span style="width:4px;height:4px"></span><span style="width:7px;height:7px"></span><span style="width:10px;height:10px"></span><span style="width:16px;height:16px"></span><span style="width:10px;height:10px"></span><span style="width:7px;height:7px"></span><span style="width:4px;height:4px"></span>
      </div>
      <div class="ribbon">
        <svg viewBox="0 0 224 46" width="224" height="46">
          <polygon points="0,14 24,14 24,44 8,44 14,29" fill="var(--brown-dark)"/>
          <polygon points="224,14 200,14 200,44 216,44 210,29" fill="var(--brown-dark)"/>
          <rect x="18" y="2" width="188" height="34" fill="var(--brown)"/>
        </svg>
        <div class="flavour">MOCHA LATTE</div>
      </div>
      <div class="volume" style="top:420px; font-size:20px;">300 ml</div>
    </div>
  </section>

  <section class="label label--modern">
    <div class="brand" style="top:76px; font-size:30px;"><span class="brand__dot"></span>Chef Tolby's</div>
    <div class="category" style="top:180px;">ICE COLD</div>
    <div class="range" style="top:258px;">BREW</div>
    <div class="dots" style="top:381px;">
      <span style="width:5px;height:5px"></span><span style="width:8px;height:8px"></span><span style="width:11px;height:11px"></span><span style="width:17px;height:17px"></span><span style="width:11px;height:11px"></span><span style="width:8px;height:8px"></span><span style="width:5px;height:5px"></span>
    </div>
    <div class="flavour-band"><div class="flavour">MOCHA LATTE</div></div>
    <div class="volume" style="top:508px; font-size:22px;">300 ml</div>
  </section>

</body>
</html>
```